Colin Vardek Business card

Hey there, I’m hoping to have a business card designed. I’m in Real estate and just switched to a new Brokerage called: The Harbourline Property Group

The back could just be the company name maybe or whatever looks good!

I’ve attached some logos of our company and some cards my buddy had done up.

On the card:
Colin Vardek
colinvardek@mailora.com
587-412-9065
colinvardek.ca

Target Market(s)

Home buyers and sellers

Industry/Entity Type

Real Estate

Contact Information for Business Card

just looking for a cool and modern design with my picture on it. I like the idea of Black and red being used.

Requirements
Must have
• all the details provided. I'm open to anything. Just want a professional looking card.

```html
<!DOCTYPE html>
<html lang="en">
<head>
<meta charset="UTF-8">
<title>Colin Vardek Business Card</title>
<link href="https://fonts.googleapis.com/css2?family=Montserrat:wght@400;500;700;800&display=swap" rel="stylesheet">
<style>
  :root {
    --page-bg: #e6e5e7;
    --card-bg: #ffffff;
    --brand-red: #d0182f;
    --ink: #0b0b0c;
    --text: #1d1d1f;
    --photo-dark: #2a3039;
    --photo-light: #e9ebee;
  }
  * { box-sizing: border-box; margin: 0; padding: 0; }
  html, body {
    width: 1200px;
    height: 1108px;
    overflow: hidden;
    background: var(--page-bg);
    font-family: "Montserrat", sans-serif;
  }
  .card {
    position: absolute;
    left: 240px;
    width: 750px;
    background: var(--card-bg);
    overflow: hidden;
  }
  .card--front { top: 62px; height: 458px; }
  .card--back { top: 590px; height: 440px; }

  .wordmark {
    position: absolute;
    display: flex;
    align-items: center;
    gap: 14px;
  }
  .wordmark__square {
    width: 22px;
    height: 22px;
    background: var(--brand-red);
    flex: none;
  }
  .wordmark__name {
    font-family: "Montserrat", sans-serif;
    font-weight: 800;
    color: var(--ink);
    text-transform: uppercase;
    line-height: 1.02;
    letter-spacing: -0.5px;
  }
  .card--front .wordmark { left: 20px; top: 36px; }
  .card--front .wordmark__name { font-size: 46px; }
  .card--back .wordmark { left: 146px; top: 148px; }
  .card--back .wordmark__name { font-size: 46px; }

  .agent {
    position: absolute;
    left: 33px;
    top: 242px;
  }
  .agent__name {
    font-size: 27px;
    font-weight: 700;
    color: var(--brand-red);
    letter-spacing: 0.2px;
  }
  .agent__title {
    font-size: 16px;
    font-weight: 500;
    color: var(--text);
    margin-top: 4px;
  }
  .contact {
    position: absolute;
    left: 32px;
    top: 328px;
    list-style: none;
  }
  .contact__item {
    display: flex;
    align-items: center;
    gap: 11px;
    height: 33px;
    font-size: 16px;
    font-weight: 500;
    color: var(--text);
  }
  .contact__icon { width: 17px; height: 17px; flex: none; }

  .portrait {
    position: absolute;
    left: 480px;
    top: 58px;
    width: 270px;
    height: 400px;
    background: linear-gradient(180deg, var(--photo-light) 0%, #c9ccd2 18%, var(--photo-dark) 45%, #1f242c 100%);
    clip-path: polygon(36% 0, 66% 0, 70% 26%, 95% 36%, 100% 100%, 0 100%, 14% 40%, 32% 27%);
  }
</style>
</head>
<body>
  <section class="card card--front">
    <div class="wordmark">
      <span class="wordmark__square"></span>
      <span class="wordmark__name">The Harbourline<br>Property Group</span>
    </div>

    <div class="agent">
      <p class="agent__name">Colin Vardek</p>
      <p class="agent__title">Owner</p>
    </div>

    <ul class="contact">
      <li class="contact__item">
        <svg class="contact__icon" viewBox="0 0 24 24" aria-hidden="true"><path fill="#d0182f" d="M6.6 10.8a15.1 15.1 0 0 0 6.6 6.6l2.2-2.2c.3-.3.7-.4 1-.2 1.1.4 2.3.6 3.6.6.6 0 1 .4 1 1V20c0 .6-.4 1-1 1A17 17 0 0 1 3 4c0-.6.4-1 1-1h3.5c.6 0 1 .4 1 1 0 1.3.2 2.5.6 3.6.1.3 0 .7-.2 1z"/></svg>
        587-412-9065
      </li>
      <li class="contact__item">
        <svg class="contact__icon" viewBox="0 0 24 24" aria-hidden="true"><rect x="2" y="5" width="20" height="14" rx="1.5" fill="#d0182f"/><path d="M3 6.5l9 6.5 9-6.5" fill="none" stroke="#fff" stroke-width="1.6"/></svg>
        colinvardek@mailora.com
      </li>
      <li class="contact__item">
        <svg class="contact__icon" viewBox="0 0 24 24" aria-hidden="true"><circle cx="12" cy="12" r="10" fill="#d0182f"/><path d="M2 12h20M12 2c3 3 3 17 0 20M12 2c-3 3-3 17 0 20" fill="none" stroke="#fff" stroke-width="1.4"/></svg>
        www.colinvardek.ca
      </li>
    </ul>

    <div class="portrait" role="img" aria-label="Portrait photo of Colin Vardek, seated, in a dark suit and white shirt"></div>
  </section>

  <section class="card card--back">
    <div class="wordmark">
      <span class="wordmark__square"></span>
      <span class="wordmark__name">The Harbourline<br>Property Group</span>
    </div>
  </section>
</body>
</html>
```